Simple and clean

We need a business card design for a new company called Dwelling Hawk. It is a search engine to find current properties for sale or rent in New Zealand market.
We have already a colour scheme that we would like people to use.
Light brown: #D4CCB0
Light green: #D6E4D4
Green: #669966
Black/White
It is OK to divert from this colour scheme slightly as long as there is a green component to the business card.
Final design should be clean, simple and should communicate the nature of the business.
Target Market(s)
- First home buyers
- Real estate agents
- People seeking rentals
Industry/Entity Type
Business
Requirements
Must have
- Use those or similar colours.
Light brown: #D4CCB0
Light green: #D6E4D4
Green: #669966
Black/White

```html
<!DOCTYPE html>
<html lang="en">
<head>
<meta charset="utf-8">
<title>Dwelling Hawk — Business Card</title>
<link rel="stylesheet" href="https://fonts.googleapis.com/css2?family=Arimo:ital,wght@0,400;0,700;1,400&display=swap">
<style>
  :root {
    --light-green: #d6e4d4;
    --green: #669966;
    --ink: #1c1f1c;
    --text: #3a3d3a;
    --label: #8a8f8a;
    --role: #9aab98;
    --rule: rgba(255, 255, 255, 0.55);
    --white: #ffffff;
    --haze: #eceeec;
  }
  * { margin: 0; padding: 0; box-sizing: border-box; }
  html, body {
    width: 1200px;
    height: 690px;
    overflow: hidden;
    background: var(--white);
  }
  .card {
    position: relative;
    width: 1200px;
    height: 690px;
    overflow: hidden;
    font-family: "Arimo", Arial, sans-serif;
    background: linear-gradient(90deg,
      var(--light-green) 0%,
      var(--light-green) 58%,
      #e6efe4 72%,
      var(--white) 90%,
      var(--white) 100%);
  }
  .brand {
    position: absolute;
    top: 86px;
    right: 58px;
    display: flex;
    align-items: center;
    gap: 8px;
  }
  .brand-mark {
    width: 14px;
    height: 14px;
    background: var(--green);
  }
  .brand-name {
    font-size: 30px;
    font-weight: 700;
    color: var(--ink);
    letter-spacing: -0.3px;
  }
  .identity {
    position: absolute;
    top: 296px;
    right: 714px;
    text-align: right;
  }
  .person-name {
    font-size: 29px;
    font-weight: 700;
    color: var(--ink);
    letter-spacing: 0.4px;
    line-height: 1.1;
  }
  .person-role {
    margin-top: 2px;
    font-size: 20px;
    font-style: italic;
    color: var(--role);
  }
  .divider {
    position: absolute;
    left: 508px;
    top: 173px;
    width: 1px;
    height: 346px;
    background: var(--rule);
  }
  .contact {
    position: absolute;
    top: 299px;
    left: 529px;
    list-style: none;
    font-size: 21px;
    line-height: 27.5px;
    color: var(--text);
  }
  .contact-label { color: var(--label); }
  .corner-art {
    position: absolute;
    right: 0;
    bottom: 0;
    width: 140px;
    height: 130px;
    background: radial-gradient(ellipse at 100% 100%, var(--haze) 0%, rgba(236, 238, 236, 0.6) 45%, rgba(255, 255, 255, 0) 75%);
  }
</style>
</head>
<body>
  <main class="card">
    <div class="brand">
      <span class="brand-mark"></span>
      <span class="brand-name">Dwelling Hawk</span>
    </div>

    <div class="identity">
      <p class="person-name">Liam Carver</p>
      <p class="person-role">Director</p>
    </div>

    <div class="divider"></div>

    <ul class="contact">
      <li><span class="contact-label">Web:</span> www.dwellinghawk.co.nz</li>
      <li><span class="contact-label">Mobil:</span> xx xxxxxx xxx</li>
      <li><span class="contact-label">E-mail:</span> liam@dwellinghawk.co.nz</li>
    </ul>

    <div class="corner-art" role="img" aria-label="Faint house illustration in the corner"></div>
  </main>
</body>
</html>
```